Pull Up Banner - Recruitment Company

We would like a design for a pull up banner.

For context: we are a recruitment business. We specialise in helping people in healthcare industry to find jobs in Australia.

I have come up with several ideas and text for the banner. Feel free to use the following as you see appropriate:

- Our logo (see attached)
- 'Healthcare Recruitment Agency'
- Some sort of imagine / cartoon of medical professionals (ie. doctor, nurse, physiotherapist, speech pathologist). A cartoon is more friendly than committing to a photo
- 'Empowering your next career move'
- 'Discover tailored opportunities based on your career preferences'
- Dot points (allied health, nursing, medical imaging)
- Contact info at the bottom including our website (www.quellastaffing.com.au, our Instagram handle @quellastaffing, Mobile: XXXX XXX XXX. The title section for contact information could be 'Get in touch:'

Feel free to submit a couple of designs and we can merge aspects that look good on your designs and find the perfect fit.
Thank you
Updates

Hello,

Thank you for your initial submissions to this project. I appreciate the time you've invested.

After reviewing the first attempt, I'd like to share some feedback and initial observations:

- Professionalism and engagement: Is the overall appearance of the banner professional? It's crucial that we have a high-quality design as this will represent our business.

- Image selection: The image (whether cartoon or real people) appears quite generic. Please consider submitting the banner with a few different photos in the middle for us to choose from. Ensure the image is a good fit and not simply a generic stock photo.

- Contact section: Kindly remove the phone number; we no longer wish to include it on the banner. Instead, please include our website (www.quellastaffing.com.au) and Instagram handle (@quellastaffing).

- Color scheme: White, black, and red/pink are preferred, or alternatively, blue. However, please avoid incorporating too many different colors as it may detract from the professional appearance.

We will be printing the design on a banner and require it to look professional and engaging.

Thank you once again for your submissions. I hope the feedback provided above is helpful.

Warm regards,

Target Market(s)

Allied Health Australia

Font styles to use
Serif

Colors
0054AA
0677BA
7BADD7
CADEEF
E8F1F8
0094D4
00A9DD
6FCCEA
C7EBF8
E9F6FB
EB3D1F
EC4F4E
F09395
F8D3D4
FCEDEE

```html
<!DOCTYPE html>
<html lang="en">
<head>
<meta charset="UTF-8">
<title>Quella Staffing – Pull Up Banner</title>
<link rel="stylesheet" href="https://fonts.googleapis.com/css2?family=Poppins:wght@500;600;700;800&display=swap">
<style>
  :root {
    --page-bg: #c4c4c4;
    --banner-bg: #ffffff;
    --navy: #00338f;
    --ink: #1a1a1a;
    --ring: #0677ba;
    --icon-grey: #555a60;
    --rule: #8a8a8a;
    --art-light: #d6f2ee;
    --art-mid: #6fc7d3;
    --art-deep: #1a8bbf;
  }
  * { margin: 0; padding: 0; box-sizing: border-box; }
  html, body {
    width: 1200px; height: 1200px; overflow: hidden;
    background: var(--page-bg);
    font-family: "Poppins", sans-serif;
  }
  .banner {
    position: absolute; left: 364px; top: 45px;
    width: 472px; height: 1110px;
    background: var(--banner-bg);
    overflow: hidden;
  }
  .brand {
    position: absolute; top: 78px; left: 0; width: 100%;
    text-align: center;
    font-weight: 700; font-size: 34px; letter-spacing: 3px;
    color: var(--ink);
  }
  .hero-art {
    position: absolute; left: 0; top: 145px; width: 472px; height: 382px;
    background: linear-gradient(180deg, var(--art-light) 0%, var(--art-mid) 55%, var(--art-deep) 100%);
  }
  .headline {
    position: absolute; top: 548px; left: 0; width: 100%;
    text-align: center; font-weight: 700;
  }
  .headline .line-blue {
    display: block; color: var(--navy);
    font-size: 48.5px; line-height: 44px; letter-spacing: -0.3px;
  }
  .headline .line-dark {
    display: block; color: var(--ink);
    font-size: 76px; line-height: 72px; letter-spacing: -1px;
  }
  .divider {
    position: absolute; top: 713px; left: 108px; width: 256px;
    height: 1px; background: var(--rule);
  }
  .tagline {
    position: absolute; top: 732px; left: 0; width: 100%;
    text-align: center; color: var(--ink);
    font-weight: 600; font-size: 26px; line-height: 31px;
  }
  .offer {
    position: absolute; top: 806px; left: 76px; width: 320px; height: 73px;
    border-radius: 18px; background: var(--navy);
    display: flex; align-items: center; justify-content: center;
    text-align: center; color: #fff;
    font-weight: 600; font-size: 15.5px; line-height: 19px;
  }
  .sectors { position: absolute; top: 905px; left: 0; width: 100%; height: 44px; }
  .sector { position: absolute; top: 0; display: flex; align-items: flex-start; gap: 6px; }
  .sector .ring {
    width: 42px; height: 42px; border-radius: 50%;
    border: 3px solid var(--ring);
    display: flex; align-items: center; justify-content: center;
    flex: none;
  }
  .sector .label {
    font-weight: 600; font-size: 14px; line-height: 17px; color: var(--ink);
    padding-top: 2px;
  }
  .sector-allied { left: 75px; }
  .sector-nursing { left: 178px; }
  .sector-medical { left: 293px; }
  .contact-title {
    position: absolute; top: 966px; left: 137px; width: 198px; height: 26px;
    border-radius: 13px; background: var(--navy);
    color: #fff; text-align: center;
    font-weight: 700; font-size: 20px; line-height: 26px;
  }
  .contact-row {
    position: absolute; top: 1003px; left: 0; width: 100%;
    display: flex; justify-content: center;
    font-weight: 600; font-size: 15px; color: var(--ink);
  }
  .contact-row span { display: flex; align-items: center; gap: 5px; }
  .social-mark {
    width: 12px; height: 12px; border: 2px solid var(--navy); border-radius: 2px;
  }
  .website {
    position: absolute; top: 1029px; left: 0; width: 100%;
    text-align: center; font-weight: 600; font-size: 19px;
    letter-spacing: 1.6px; color: var(--ink);
  }
  .website .domain { color: var(--navy); }
</style>
</head>
<body>
  <div class="banner">
    <div class="brand">QUELLA STAFFING</div>

    <div class="hero-art" role="img" aria-label="Illustration of a group of healthcare professionals — surgeon, nurses, doctor in a white coat and staff in protective gear — standing among large blue leaves"></div>

    <h1 class="headline">
      <span class="line-blue">HEALTHCARE</span>
      <span class="line-blue">RECRUITMENT</span>
      <span class="line-dark">AGENCY</span>
    </h1>

    <div class="divider"></div>

    <p class="tagline">Empowering your next<br>career move</p>

    <div class="offer">Discover tailored opportunities<br>based on your career preferences</div>

    <div class="sectors">
      <div class="sector sector-allied">
        <div class="ring">
          <svg width="22" height="20" viewBox="0 0 22 20">
            <path d="M11 19 C4 13 1 10 1 6 A5 5 0 0 1 11 4 A5 5 0 0 1 21 6 C21 10 18 13 11 19Z" fill="var(--icon-grey)"/>
            <path d="M9.5 6.5h3v3h3v3h-3v3h-3v-3h-3v-3h3z" fill="#fff"/>
          </svg>
        </div>
        <div class="label">Allied<br>health</div>
      </div>
      <div class="sector sector-nursing">
        <div class="ring">
          <svg width="20" height="22" viewBox="0 0 20 22">
            <rect x="5" y="1" width="10" height="4" rx="1" fill="var(--icon-grey)"/>
            <circle cx="10" cy="9" r="4" fill="var(--icon-grey)"/>
            <path d="M2 21 C2 15 5 13.5 10 13.5 C15 13.5 18 15 18 21Z" fill="var(--icon-grey)"/>
          </svg>
        </div>
        <div class="label">Nursing</div>
      </div>
      <div class="sector sector-medical">
        <div class="ring">
          <svg width="20" height="22" viewBox="0 0 20 22">
            <path d="M10 1 L18 4 V10 C18 15 14.5 19 10 21 C5.5 19 2 15 2 10 V4Z" fill="var(--icon-grey)"/>
            <circle cx="10" cy="11" r="4.5" fill="#fff"/>
            <path d="M9 8.5h2v1.5h1.5v2H11v1.5H9V12H7.5v-2H9z" fill="var(--icon-grey)"/>
          </svg>
        </div>
        <div class="label">Medical</div>
      </div>
    </div>

    <div class="contact-title">GET IN TOUCH</div>

    <div class="contact-row">
      <span><i class="social-mark"></i>@quellastaffing</span>
    </div>

    <div class="website">www.<span class="domain">quellastaffing</span>.com.au</div>
  </div>
</body>
</html>
```